Mobile Repair Service on location needs a Web Design

We are starting a new mobile device repair service called Handset Haven and our website needs a design!

Hello Designers!
First, we'd like to make clear this is more than a simple web design contest, we want the designers to create an idea. We want someone who can create the whole theme of the service's we provide. We want someone that can help design our visual branding, help us communicate a sentiment. And we are willing to pay for that.

Who are we?
Our company is based in Rotterdam, the Netherlands. We provide different services for all kinds of electronic devices. The kind of services we provide are, among other things, installations of hardware and software and the repair of broken or malfunctioning devices.
We are starting a new service that offers mobile device repairs on location, be it at the home of our customers, their office, or any other place. Just give us the address and we will come to you for the repair job. This is also our main USP. We have multiple skilled engineers who drive trough the country on a daily basis and can be on location within a working day. Repair is done immediately onsite while the customer waits. At this stage we will start with the smartphone product-group within the mobile devices. In a second phase we might also add tablets.
People don't want to be without their phone for weeks because of some parts that needed to be ordered by a repair center they had to sent their phone to. We offer a fully functional mobile repair center in the form of specially customized vans. These vans have all the tools and utilities needed by our engineers to safely repair your mobile device. Your phone is being repaired directly in front of you, the next business-day, on a location you desire.

For this new service we are creating a website called Handset Haven. The website needs a story and matching design and this is where you come in. We are not looking for a simple template design we can get from any place. We need a story. We want you to create an idea, build a unique theme or vision that helps sell the product/service. This goes beyond the design of the website. We need the whole package, the design you are creating needs to have returning elements like icons, color use, images, maybe even characters etc. You name it! There needs to be a common thread in the design so we can reuse elements in, for example, the email templates, the work order or receipt we give to our customers (we may contact the winner of the contest to design these for us as well!).

The name 'Handset Haven' is chosen. Rehab (short for rehabilitate) has a bold and playful tone to it and the design needs to reflect the name. So we're looking for a somewhat playful and cheeky design. Definitely not too serious and definitely modern. We already got a logo that we love and that fit's this description (see attached design documents for the logo). It's bold, powerful and fun. Our web design needs to reflect this as well and has to fit in with our logo.
We would really like it if the design somehow incorporates elements that highlight our unique selling points (repairs on location, we come to you etc.). We would really like some form of story telling in the design. Think clumsy people breaking their phones. Teenagers in tears because they have no access to their friends. People nowadays have the need to always be 'connected'. What happens when your phone is broken or malfunctioning? We're handling tech, we are nerds and a little bit weird, but we're professionals and here to help you with your problem. The sentiment Byte Brigade tries to communicate is something we really like. We're looking for fresh idea's, anything goes!

In an overview all Unique Selling Points of the Handset haven service:
- Professional service on location. Don’t ship to us we will come to you!
- Clear pricing upfront. No hidden cost.
- Next business-day repair.
- Backed by a professional call center open 12 hours a day and open on a Saturday as well
- Backed by a professional repair center with more then 12 years of experience
- Repair is done by certified engineers
- 1 year warranty on the repair

The process:
The main function of our website will be for customers to make a repair request. A customer will visit our website and can make a repair request immediately by going through a 'request-order-flow'. In this flow he or she will need to fill in some forms and can select wich type/model/brand of mobile device he or she has and what parts need to be repaired. After a request is placed we will call the customer back (within an hour) for a short intake and to set a date/time and location. Our engineer will meet the customer at the specified location and will repair the device onsite in one of our mobile repair centers, which is a specialized van equipped with all the tools needed for device restorations.
So in short the steps are:
- Choose your device and repair job
- Place the order
- Get a callback within the hour
- Set date and location
- We will come to you.

Website functionality:
Our website is our main form of communication. So the sentiment we want to communicate needs be reflected in the design. We need a main/front page designed (preferably a long scrolling page design) containing:
1. Customers will be able to request a repair job directly on our website. So there will need to be a prominent button/link at the top of our main page that will bring the customer to this 'request-order-flow'. This is the main flow which needs to be full focus on the front page. All other items are secondary.
2. The general information of who we are and what we do, and why the customer should choose us. Preferably in short bullet-point type keywords/sentences with icons or other visual cues. See our unique selling points to get an idea of the information that will be displayed here.
3. There needs to be a section that will explain the process (see above) of a repair request step-by- step, again in brief short key sentences and with (custom) icons.
4. There needs to be a section that explains to the customer he/she can always contact us if they are not sure what the problem is with their device, and for this reason are not sure what repair request they should order.
5. We want to implement some functionality that display customer ratings or customer reviews. So there needs to be room for some kind of widget of plugin we're going to implement which shows these reviews.
6. A 'For business section' where we will explain all the options we provide for corporate clients.
7. Social media links.
8. There needs to be a menu with buttons that leads to the all sections described in the previous points.

For now, we need a design for our front page. In the second phase, when we have picked our winner, we may ask the winner to design the page(s) for our request workflow as well.

EDIT:
Finally, we have a very specific order in mind for the different segments of our website. We would like you to add some more segments that were not in our original brief as well:

1. Top header with order/request button. (should instantly make clear our main USP, we do repairs on location)
2. Our process
3. Our unique selling points / why choose us
4. The kind of repairs we do (broken screens, broken batteries, water damage, broken camera's, no sound etc.)
5. A 'meet our team' section, where we introduce some of our engineers
6. A 'contact us for any questions' section/
7. Testimonials/user reviews
8. A section where we show key performance indicators
9. 'For businesses' sections
10.'Subscribe for newsletter' field
11. Social media buttons

Industry/Entity Type

It Service

Number of Pages Required

1 page

Font styles to use
Sans Serif

Requirements
Must have
• a main/front page, design only
• custom icons/images for banners, adverts online and in print (high res)
Nice to have
• Storytelling in our design.
• Design that fits with our brand new logo.
• Elements like icons to have a flat design.
• Keep in mind that the website will need to be responsive when designing! (Ideally provide an example of the mobile design as well)
• Create a fun and trustworthy feeling.

```html
<!DOCTYPE html>
<html lang="en">
<head>
<meta charset="utf-8">
<title>Handset Haven – Mobile Repair On Location</title>
<link href="https://fonts.googleapis.com/css2?family=Oswald:wght@400;500;700&family=Roboto:ital,wght@0,400;0,500;0,700;1,400&display=swap" rel="stylesheet">
<style>
:root{
  --orange:#f26522;
  --orange-dark:#d9541a;
  --ink:#222222;
  --text:#666666;
  --muted:#999999;
  --line:#e3e3e3;
  --dark:#3b3b3b;
  --footer:#3d3d3d;
  --cream:#fdf8dc;
  --lavender:#b9b5dd;
  --white:#ffffff;
}
*{box-sizing:border-box;margin:0;padding:0}
html,body{width:1200px;height:3822px;overflow:hidden}
body{position:relative;background:var(--white);font-family:'Roboto',Arial,sans-serif;color:var(--text)}
.abs{position:absolute}
.heading{font-family:'Oswald','Arial Narrow',sans-serif;font-weight:500;color:var(--ink);text-transform:uppercase;letter-spacing:.5px}

/* Header */
.site-header{left:0;top:0;width:1200px;height:97px;background:var(--white);border-bottom:1px solid var(--line)}
.brand{left:178px;top:12px;display:flex;align-items:center;gap:12px}
.brand-dot{width:58px;height:58px;border-radius:50%;background:var(--orange)}
.brand-name{font-family:'Oswald',sans-serif;font-weight:700;font-size:30px;line-height:28px;color:var(--dark);text-transform:uppercase;width:120px}
.brand-tag{left:250px;top:75px;font-size:11px;color:var(--orange);font-weight:500}
.topbar{top:10px;left:425px;display:flex;align-items:center;font-size:12px;color:var(--text);height:22px}
.topbar .item{display:flex;align-items:center;gap:6px;margin-right:22px;white-space:nowrap}
.topbar b{color:var(--ink)}
.ico-round{width:22px;height:22px;border-radius:50%;background:var(--orange);display:flex;align-items:center;justify-content:center}
.socials{left:906px;top:9px;display:flex;gap:9px}
.socials span{width:24px;height:24px;border-radius:4px;background:#c9c9c9}
.main-nav{left:470px;top:52px;display:flex;height:45px;align-items:center}
.main-nav a{font-family:'Oswald',sans-serif;font-size:14px;color:var(--ink);text-decoration:none;padding:0 18px;height:45px;line-height:45px}
.main-nav a.active{border-bottom:3px solid var(--orange)}
.btn-request{left:848px;top:52px;width:182px;height:45px;background:var(--orange);color:var(--white);font-family:'Oswald',sans-serif;font-size:14px;display:flex;align-items:center;justify-content:center;text-transform:uppercase}

/* Hero */
.hero{left:0;top:97px;width:1200px;height:515px;background:linear-gradient(100deg,#2a2d30 0%,#5c5f62 45%,#8a8c8e 65%,#3d4144 100%)}
.hero-title{left:173px;top:185px;color:var(--white)}
.hero-title .l1{font-family:'Oswald',sans-serif;font-size:38px;letter-spacing:4px;line-height:44px}
.hero-title .l2{font-family:'Oswald',sans-serif;font-weight:700;font-size:56px;letter-spacing:3px;line-height:58px}
.hero-bar{left:0;top:288px;width:700px;height:38px;background:var(--orange);color:var(--white);font-family:'Oswald',sans-serif;font-size:24px;line-height:38px;padding-left:173px}
.hero-dots{left:552px;top:554px;display:flex;gap:9px}
.hero-dots span{width:10px;height:10px;border-radius:50%;background:rgba(255,255,255,.6)}
.hero-dots span.on{background:var(--orange)}

/* About */
.section-title{font-size:22px}
.rule{width:40px;height:2px;background:var(--orange);margin-top:8px}
.about{left:173px;top:656px;width:410px}
.about p{font-size:12.5px;line-height:20px;margin-top:18px}
.about h2{margin-top:36px}
.about h2:first-child{margin-top:0}
.checks{list-style:none;margin-top:20px}
.checks li{font-size:12.5px;line-height:28px;display:flex;align-items:center;gap:10px}
.about-photo{left:612px;top:657px;width:488px;height:604px;background:linear-gradient(160deg,#dfe4ea 0%,#6b86a8 40%,#2f4b78 65%,#f2f2f2 85%)}

/* Why */
.why{left:0;top:1366px;width:1200px;height:622px;background:linear-gradient(120deg,#9eb0c4,#3a5a8a 60%,#d8d8d8)}
.why-orange{left:0;top:0}
.why-badge{left:291px;top:1692px;width:124px;height:124px;border-radius:50%;background:var(--white);border:6px solid var(--orange)}
.why-title{left:520px;top:1402px;width:590px;text-align:center;color:var(--white);font-size:24px}
.usp{width:130px;text-align:center;color:var(--white);font-size:11.5px;font-weight:700;line-height:16px}
.usp .ico{width:84px;height:84px;border-radius:50%;background:var(--dark);margin:0 auto 14px;display:flex;align-items:center;justify-content:center;border:3px solid rgba(255,255,255,.15)}

/* Process */
.process-title{left:0;top:2036px;width:1200px;text-align:center;font-size:22px}
.step{width:170px;text-align:center;font-size:12px;color:var(--ink);line-height:17px}
.step .ico{width:94px;height:94px;border-radius:50%;border:3px solid #e4e4e4;background:var(--white);margin:0 auto 16px;display:flex;align-items:center;justify-content:center}
.step-arrow{color:#bbb;font-size:22px}

/* Request */
.request-band{left:0;top:2286px;width:1200px;height:340px;background:var(--cream)}
.mascot{left:127px;top:2306px;width:204px;height:180px;border-radius:12px;background:linear-gradient(180deg,#f7c77a,#9aa4ad 55%,#5b6670)}
.pin{left:372px;top:2290px;width:44px;height:44px;border-radius:50%;background:var(--orange)}
.request-form{left:382px;top:2324px;width:612px;height:250px;border:3px solid var(--orange);background:var(--cream)}
.request-form h3{position:absolute;top:16px;left:0;width:100%;text-align:center;font-size:22px}
.field{position:absolute;height:36px;border:1px solid #d8d8d8;background:var(--white);font-size:12px;color:var(--muted);line-height:34px;padding-left:12px}
.field .caret{position:absolute;right:14px;top:0;color:var(--orange)}
.radios{position:absolute;left:462px;top:134px;font-size:12px;color:var(--ink);display:flex;gap:22px}
.radios span{display:flex;align-items:center;gap:6px}
.radios i{width:12px;height:12px;border-radius:50%;border:1px solid #999;display:inline-block}
.radios i.on{background:var(--orange);border-color:var(--orange)}
.btn-order{position:absolute;left:23px;top:183px;width:560px;height:40px;background:var(--orange);color:var(--white);font-family:'Oswald',sans-serif;font-size:15px;text-align:center;line-height:40px}

/* Testimonials */
.reviews{left:0;top:2540px;width:1200px;height:480px}
.reviews-title{left:0;top:2652px;width:1200px;text-align:center;font-size:22px}
.review{width:420px;height:242px;top:2726px;background:var(--white);box-shadow:0 2px 6px rgba(0,0,0,.12)}
.review .quote{position:absolute;left:188px;top:14px;font-family:'Oswald',sans-serif;font-size:44px;color:var(--ink);line-height:44px}
.review .stars{position:absolute;right:22px;top:22px;color:var(--orange);font-size:14px;letter-spacing:1px}
.review p{position:absolute;left:28px;top:62px;width:364px;font-size:12px;font-style:italic;line-height:19px;text-align:center}
.review .who{position:absolute;left:120px;top:172px;display:flex;align-items:center;gap:14px}
.avatar{width:48px;height:48px;border-radius:50%;background:#cfcfcf}
.who b{display:block;font-size:12px;color:var(--ink)}
.who small{font-size:11px}

/* Corporate */
.corp-title{left:0;top:3058px;width:1200px;text-align:center;font-size:22px}
.corp{width:273px;top:3134px}
.corp .img{height:186px;background:linear-gradient(135deg,#16242f,#3d6a86 55%,#b7c8d3)}
.corp h4{margin-top:16px;font-size:15px;line-height:20px;color:var(--ink);font-weight:700}
.corp p{margin-top:14px;font-size:11px;line-height:16px;color:var(--muted)}
.btn-small{margin-top:18px;width:72px;height:24px;background:var(--orange);color:var(--white);font-size:11px;line-height:24px;text-align:center}

/* Footer */
.site-footer{left:0;top:3555px;width:1200px;height:267px;background:var(--footer);color:#cfcfcf}
.up-tab{left:560px;top:3535px;width:80px;height:30px;border-radius:40px 40px 0 0;background:var(--footer);color:var(--white);text-align:center;line-height:34px;font-size:16px}
.f-brand{left:171px;top:3608px;display:flex;align-items:center;gap:12px}
.f-brand .brand-dot{width:70px;height:70px}
.f-brand .brand-name{color:var(--white);font-size:32px;line-height:30px;width:130px}
.f-btn{left:171px;top:3720px;width:172px;height:38px;border-radius:20px;background:var(--orange);color:var(--white);font-family:'Oswald',sans-serif;font-size:13px;line-height:38px;text-align:center}
.f-copy{left:171px;top:3778px;font-size:11px;color:#cfcfcf}
.f-col{top:3608px;font-size:11.5px;line-height:18px;color:#cfcfcf}
.f-col h5{font-family:'Oswald',sans-serif;font-size:13px;color:var(--white);font-weight:500;margin-bottom:12px}
.f-col .big{font-size:17px;color:var(--white);font-weight:500}
.subscribe{display:flex;margin-top:12px}
.subscribe span{width:190px;height:30px;background:var(--white);color:var(--muted);font-size:11px;line-height:30px;padding-left:10px}
.subscribe b{width:80px;height:30px;background:var(--orange);color:var(--white);font-size:11px;line-height:30px;text-align:center}
.f-social{display:flex;gap:12px;margin-top:10px}
.f-social span{width:22px;height:22px;border-radius:50%;border:2px solid #8e8e8e}
</style>
</head>
<body>

<!-- Header -->
<header class="abs site-header">
  <div class="abs brand"><span class="brand-dot"></span><span class="brand-name">Handset Haven</span></div>
  <div class="abs brand-tag">We will come to you!</div>
  <div class="abs topbar">
    <div class="item"><span class="ico-round"><svg width="12" height="12" viewBox="0 0 24 24"><path d="M6.6 10.8a15 15 0 006.6 6.6l2.2-2.2a1 1 0 011-.25 11.4 11.4 0 003.6.57 1 1 0 011 1V20a1 1 0 01-1 1A17 17 0 013 4a1 1 0 011-1h3.5a1 1 0 011 1c0 1.25.2 2.45.57 3.57a1 1 0 01-.25 1z" fill="#fff"/></svg></span>Call Us Today: <b>(100) 000-000</b></div>
    <div class="item"><span class="ico-round"><svg width="12" height="12" viewBox="0 0 24 24"><rect x="2" y="5" width="20" height="14" rx="2" fill="none" stroke="#fff" stroke-width="2"/><path d="M2 6l10 7 10-7" fill="none" stroke="#fff" stroke-width="2"/></svg></span>Email Us : <b>info@handsethaven.com</b></div>
  </div>
  <div class="abs socials"><span></span><span></span><span></span><span></span></div>
  <nav class="abs main-nav">
    <a class="active">HOME</a><a>ABOUT US</a><a>SERVICES</a><a>CONTACT US</a>
  </nav>
  <div class="abs btn-request">Request Order Flow</div>
</header>

<!-- Hero -->
<section class="abs hero" role="img" aria-label="Photo of a smiling repair engineer at the wheel of his service van"></section>
<div class="abs hero-title"><div class="l1">PROFESSIONAL SERVICE</div><div class="l2">ON LOCATION.</div></div>
<div class="abs hero-bar">DON'T SHIP TO US WE WILL COME TO YOU!</div>
<div class="abs hero-dots"><span class="on"></span><span></span><span></span><span></span><span></span></div>

<!-- About -->
<section class="abs about">
  <h2 class="heading section-title">Who we are</h2><div class="rule"></div>
  <p>Lorem ipsum dolor sit amet, consectetur adipiscing elit, sed do eiusmod tempor incididunt ut labore et dolore magna aliqua. Ut enim ad minim veniam, quis nostrud exercitation ullamco laboris nisi ut aliquip ex ea commodo consequat. Duis aute irure dolor in reprehenderit in voluptate velit esse cillum dolore eu fugiat nulla pariatur. Excepteur sint occaecat cupidatat non proident, sunt in culpa qui officia deserunt mollit anim id est laborum.</p>
  <p>Lorem ipsum dolor sit amet, consectetur adipiscing elit, sed do eiusmod tempor incididunt ut labore et dolore magna aliqua. Ut enim ad minim veniam, quis nostrud exercitation ullamco laboris nisi ut aliquip ex ea commodo consequat.</p>
  <h2 class="heading section-title">What we do</h2><div class="rule"></div>
  <p>Lorem ipsum dolor sit amet, consectetur adipiscing elit, sed do eiusmod tempor incididunt ut labore et dolore magna aliqua. Ut enim ad minim veniam, quis nostrud exercitation ullamco.</p>
  <ul class="checks">
    <li><svg width="14" height="14" viewBox="0 0 24 24"><path d="M3 13l6 6L21 5" fill="none" stroke="#f26522" stroke-width="3"/></svg>Lorem ipsum dolor sit amet, consectetur adipiscing elit.</li>
    <li><svg width="14" height="14" viewBox="0 0 24 24"><path d="M3 13l6 6L21 5" fill="none" stroke="#f26522" stroke-width="3"/></svg>Fusce ornare dolor erat quis dignissim, sed imperdiet purus mattis.</li>
    <li><svg width="14" height="14" viewBox="0 0 24 24"><path d="M3 13l6 6L21 5" fill="none" stroke="#f26522" stroke-width="3"/></svg>Vivamus pulvinar neque ac scelerisque semper.</li>
    <li><svg width="14" height="14" viewBox="0 0 24 24"><path d="M3 13l6 6L21 5" fill="none" stroke="#f26522" stroke-width="3"/></svg>Mauris vulputate tortor vel sapien ornare fringilla.</li>
    <li><svg width="14" height="14" viewBox="0 0 24 24"><path d="M3 13l6 6L21 5" fill="none" stroke="#f26522" stroke-width="3"/></svg>Fusce imperdiet nunc at tempor pretium.</li>
  </ul>
</section>
<div class="abs about-photo" role="img" aria-label="Photo of an engineer in a blue uniform with a tablet beside a white branded service van"></div>

<!-- Why choose us -->
<section class="abs why" role="img" aria-label="Photo of a smiling engineer in a cap holding a tablet">
  <svg class="abs why-orange" width="1200" height="622" viewBox="0 0 1200 622"><polygon points="535,0 1200,0 1200,622 395,622" fill="#f26522"/></svg>
</section>
<div class="abs why-badge"></div>
<h2 class="abs heading why-title">Why the customer should choose us</h2>

<div class="abs usp" style="left:536px;top:1498px"><div class="ico"><svg width="36" height="36" viewBox="0 0 24 24"><path d="M12 2a7 7 0 00-7 7c0 5 7 13 7 13s7-8 7-13a7 7 0 00-7-7z" fill="none" stroke="#fff" stroke-width="1.6"/><circle cx="12" cy="9" r="2.5" fill="none" stroke="#fff" stroke-width="1.6"/></svg></div>Professional service on location. Don't ship to us we will come to you!</div>
<div class="abs usp" style="left:679px;top:1498px"><div class="ico"><svg width="36" height="36" viewBox="0 0 24 24"><rect x="3" y="6" width="18" height="13" rx="2" fill="none" stroke="#fff" stroke-width="1.6"/><path d="M15 12h6v4h-6z" fill="none" stroke="#fff" stroke-width="1.6"/><path d="M5 6l10-3 1 3" fill="none" stroke="#fff" stroke-width="1.6"/></svg></div>Clear pricing upfront.<br>No hidden cost.</div>
<div class="abs usp" style="left:824px;top:1498px"><div class="ico"><svg width="38" height="38" viewBox="0 0 24 24"><path d="M2 7h12v9H2zM14 10h4l3 3v3h-7z" fill="none" stroke="#fff" stroke-width="1.6"/><circle cx="6" cy="17.5" r="1.8" fill="#3b3b3b" stroke="#fff" stroke-width="1.6"/><circle cx="17" cy="17.5" r="1.8" fill="#3b3b3b" stroke="#fff" stroke-width="1.6"/></svg></div>Next business-day repair.</div>

<div class="abs usp" style="left:462px;top:1702px"><div class="ico"><svg width="36" height="36" viewBox="0 0 24 24"><rect x="4" y="3" width="16" height="18" rx="2" fill="none" stroke="#fff" stroke-width="1.6"/><circle cx="12" cy="10" r="3" fill="none" stroke="#fff" stroke-width="1.6"/><path d="M8 17h8" stroke="#fff" stroke-width="1.6"/></svg></div>Repair is done by certified engineers</div>
<div class="abs usp" style="left:603px;top:1702px"><div class="ico"><svg width="38" height="38" viewBox="0 0 24 24"><path d="M12 2l8 3v6c0 5-3.5 9-8 11-4.5-2-8-6-8-11V5z" fill="none" stroke="#fff" stroke-width="1.6"/><path d="M8 12l3 3 5-6" fill="none" stroke="#fff" stroke-width="1.6"/></svg></div>1 year warranty on<br>the repair</div>
<div class="abs usp" style="left:753px;top:1702px"><div class="ico"><svg width="36" height="36" viewBox="0 0 24 24"><path d="M14 4l6 6-9 9H5v-6z" fill="none" stroke="#fff" stroke-width="1.6"/><path d="M12 6l6 6" stroke="#fff" stroke-width="1.6"/></svg></div>Backed by a professional repair center with more then 12 years of experience</div>
<div class="abs usp" style="left:903px;top:1702px"><div class="ico"><svg width="36" height="36" viewBox="0 0 24 24"><circle cx="12" cy="9" r="4" fill="none" stroke="#fff" stroke-width="1.6"/><path d="M4 21c1-4 4-6 8-6s7 2 8 6M5 10V8a7 7 0 0114 0v2" fill="none" stroke="#fff" stroke-width="1.6"/></svg></div>Backed by a professional call center open 12 hours a day and open on a Saturday as well</div>

<!-- Process -->
<h2 class="abs heading process-title">The process</h2>
<div class="abs step" style="left:175px;top:2107px"><div class="ico"><svg width="34" height="40" viewBox="0 0 24 28"><rect x="5" y="2" width="14" height="24" rx="2" fill="none" stroke="#f26522" stroke-width="1.6"/><circle cx="12" cy="22" r="1.2" fill="#f26522"/></svg></div>Choose your device<br>and repair job</div>
<div class="abs step" style="left:346px;top:2107px"><div class="ico"><svg width="40" height="40" viewBox="0 0 24 24"><path d="M2 4h3l3 11h11l2-8H7" fill="none" stroke="#f26522" stroke-width="1.6"/><circle cx="9" cy="19" r="1.6" fill="none" stroke="#f26522" stroke-width="1.6"/><circle cx="17" cy="19" r="1.6" fill="none" stroke="#f26522" stroke-width="1.6"/><path d="M11 10l2 2 3-4" fill="none" stroke="#f26522" stroke-width="1.6"/></svg></div>Place the order</div>
<div class="abs step" style="left:519px;top:2107px"><div class="ico"><svg width="38" height="38" viewBox="0 0 24 24"><circle cx="12" cy="12" r="10" fill="none" stroke="#f26522" stroke-width="1.6"/><path d="M8.5 7.5l2 2-1 1.5a7 7 0 003.5 3.5l1.5-1 2 2-1.5 1.5c-3.5 0-8-4.5-8-8z" fill="#f26522"/></svg></div>Get a callback<br>within the hour</div>
<div class="abs step" style="left:690px;top:2107px"><div class="ico"><svg width="38" height="38" viewBox="0 0 24 24"><rect x="3" y="5" width="18" height="16" rx="2" fill="none" stroke="#f26522" stroke-width="1.6"/><path d="M3 10h18M8 3v4M16 3v4" stroke="#f26522" stroke-width="1.6"/><circle cx="16" cy="16" r="2" fill="#f26522"/></svg></div>Set date and<br>location</div>
<div class="abs step" style="left:858px;top:2107px"><div class="ico"><svg width="42" height="42" viewBox="0 0 24 24"><path d="M2 7h12v9H2zM14 10h4l3 3v3h-7z" fill="none" stroke="#f26522" stroke-width="1.6"/><circle cx="6" cy="17.5" r="1.8" fill="#fff" stroke="#f26522" stroke-width="1.6"/><circle cx="17" cy="17.5" r="1.8" fill="#fff" stroke="#f26522" stroke-width="1.6"/></svg></div>We will come to you</div>
<div class="abs step-arrow" style="left:340px;top:2138px">→</div>
<div class="abs step-arrow" style="left:512px;top:2138px">→</div>
<div class="abs step-arrow" style="left:684px;top:2138px">→</div>
<div class="abs step-arrow" style="left:852px;top:2138px">→</div>

<!-- Repair request -->
<section class="abs request-band"></section>
<div class="abs mascot" role="img" aria-label="Illustration of a cartoon repair engineer standing beside a smiling smartphone character"></div>
<div class="abs pin"></div>
<form class="abs request-form">
  <h3 class="heading">A repair request</h3>
  <div class="field" style="left:23px;top:61px;width:560px">What parts need to be repaired</div>
  <div class="field" style="left:23px;top:123px;width:191px">Model<span class="caret">⌄</span></div>
  <div class="field" style="left:239px;top:123px;width:196px">Brand<span class="caret">⌄</span></div>
  <div class="radios"><span><i class="on"></i>He</span><span><i></i>She</span></div>
  <div class="btn-order">PLACE THE ORDER</div>
</form>

<!-- Testimonials -->
<svg class="abs reviews" width="1200" height="480" viewBox="0 0 1200 480">
  <path d="M0,60 C150,20 250,100 420,70 C560,45 640,0 800,40 C950,80 1060,20 1200,50 L1200,430 L0,430 Z" fill="#b9b5dd"/>
  <path d="M0,445 C200,395 380,470 600,430 C800,395 960,470 1200,425 L1200,445 C960,495 800,420 600,455 C380,495 200,420 0,470 Z" fill="#111"/>
  <path d="M0,420 C200,380 380,455 600,418 C800,380 960,455 1200,410 L1200,428 C960,472 800,400 600,438 C380,475 200,400 0,445 Z" fill="#b9b5dd"/>
</svg>
<h2 class="abs heading reviews-title">What our customers say</h2>
<article class="abs review" style="left:171px">
  <span class="quote">“</span><span class="stars">★★★★★</span>
  <p>Lorem ipsum dolor sit amet, consectetur adipiscing elit, sed do eiusmod tempor incididunt ut labore et dolore magna aliqua. Ut enim ad minim veniam, quis nostrud exercitation ullamco laboris nisi ut aliquip ex ea commodo consequat.</p>
  <div class="who"><span class="avatar"></span><div><b>Sam Ridley</b><small>Lorem ipsum dolor</small></div></div>
</article>
<article class="abs review" style="left:612px">
  <span class="stars">★★★★★</span>
  <p>Lorem ipsum dolor sit amet, consectetur adipiscing elit, sed do eiusmod tempor incididunt ut labore et dolore magna aliqua. Ut enim ad minim veniam, quis nostrud exercitation ullamco laboris nisi ut aliquip ex ea commodo consequat.</p>
  <div class="who"><span class="avatar"></span><div><b>Nora Vale</b><small>Lorem ipsum dolor</small></div></div>
</article>

<!-- Corporate -->
<h2 class="abs heading corp-title">We provide for corporate clients</h2>
<div class="abs corp" style="left:171px">
  <div class="img" role="img" aria-label="Photo of a hand touching a glowing digital network"></div>
  <h4>Lorem ipsum dolor sit amet, consectetur adipiscing elit,</h4>
  <p>Sed ut perspiciatis unde omnis iste natus error sit voluptatem accusantium doloremque laudantium, totam rem aperiam, eaque ipsa quae ab illo inventore veritatis.</p>
  <div class="btn-small">Read More</div>
</div>
<div class="abs corp" style="left:464px">
  <div class="img" role="img" aria-label="Photo of a smiling support agent wearing a headset" style="background:linear-gradient(135deg,#6e4a36,#c79a7c 55%,#e9e1da)"></div>
  <h4>Lorem ipsum dolor sit amet, consectetur adipiscing elit,</h4>
  <p>Sed ut perspiciatis unde omnis iste natus error sit voluptatem accusantium doloremque laudantium, totam rem aperiam, eaque ipsa quae ab illo inventore veritatis.</p>
  <div class="btn-small">Read More</div>
</div>
<div class="abs corp" style="left:757px">
  <div class="img" role="img" aria-label="Photo of a business hand pointing at interlocking gear graphics" style="background:linear-gradient(135deg,#1d5a6b,#5fa7b8 55%,#d7eef2)"></div>
  <h4>Lorem ipsum dolor sit amet, consectetur adipiscing elit,</h4>
  <p>Sed ut perspiciatis unde omnis iste natus error sit voluptatem accusantium doloremque laudantium, totam rem aperiam, eaque ipsa quae ab illo inventore veritatis.</p>
  <div class="btn-small">Read More</div>
</div>

<!-- Footer -->
<footer class="abs site-footer"></footer>
<div class="abs up-tab">↑</div>
<div class="abs f-brand"><span class="brand-dot"></span><span class="brand-name">Handset Haven</span></div>
<div class="abs f-btn">REQUEST ORDER FLOW</div>
<div class="abs f-copy">© 2017 Handset Haven</div>
<div class="abs f-col" style="left:427px">
  <h5>QUICK LINKS</h5>Home<br>About Us<br>Services<br>Contact Us
</div>
<div class="abs f-col" style="left:568px">
  <h5>CONTACT US</h5>Handset Haven<br>Lorem ipsum dolor<br>City<br><br>Phone<br><span class="big">(100) 000-000</span><br><br>Email<br>info@handsethaven.com
</div>
<div class="abs f-col" style="left:757px">
  <h5>NEWSLETTER SUBSCRIBE</h5>Enter your email address below and get<br>the latest!
  <div class="subscribe"><span>Enter your Email Id here...</span><b>SUBSCRIBE</b></div>
  <h5 style="margin-top:20px;margin-bottom:0">GET CONNECT WITH US</h5>
  <div class="f-social"><span></span><span></span><span></span><span></span></div>
</div>

</body>
</html>
```